BUSINESS CARD - HALLORAN FIELD SERVICES

I would like to create a business card for my fertilizer spreading business. I would like to incorporate my existing logo and also a description of the services offered. The business card will be given to farmers so must be kept simple but effective. It will also be left in stores so much also be eye catching in order to stand out from other cards.

Target Market(s)

FARMERS

Requirements
Must have
• FRONT OF CARD = EXISTING LOGO + "CUSTOMISED SPREADING" below the logo

REAR Of CARD = SERVICES OFFERED AND CONTACT DETAILS

- Bulk fertilizer including Lime, Gypsum, Manure & Compost
- Granular fertilizer including Single Super, Urea, Gran-am, & Custom Blends
- Modern equipment - Autosteer & Variable Rate Capable
- Friendly & Reliable Service
- Contact Gus: 0417 552 308
Nice to have
• utilize same color scheme as existing logo

```html
<!DOCTYPE html>
<html lang="en">
<head>
<meta charset="utf-8">
<title>Halloran Field Services – Business Card</title>
<link rel="stylesheet" href="https://fonts.googleapis.com/css2?family=Lato:ital,wght@0,400;0,700;0,900;1,400;1,900&display=swap">
<style>
  :root {
    --backdrop: #8c8c8c;
    --card: #ffffff;
    --orange: #f7941d;
    --charcoal: #58595b;
    --ink: #3a3a3a;
  }
  * { box-sizing: border-box; margin: 0; padding: 0; }
  html, body { width: 1200px; height: 1200px; overflow: hidden; }
  body {
    background: var(--backdrop);
    font-family: "Lato", sans-serif;
    position: relative;
  }
  .card {
    position: absolute;
    left: 182px;
    width: 841px;
    height: 479px;
    background: var(--card);
    overflow: hidden;
  }
  .card--front { top: 93px; }
  .card--back { top: 621px; }

  .brand-mark {
    position: absolute;
    border-radius: 50%;
    background: var(--charcoal);
  }
  .brand-name {
    position: absolute;
    left: 0; right: 0;
    text-align: center;
    color: var(--charcoal);
    font-weight: 700;
    line-height: 1;
  }

  .front__mark { left: 347px; top: 35px; width: 160px; height: 160px; }
  .front__name { top: 214px; font-size: 50px; letter-spacing: -0.5px; }
  .front__sub { top: 264px; font-size: 24px; letter-spacing: 5px; }

  .field {
    position: absolute;
    left: 0; right: 0;
  }
  .field--gold { top: 300px; height: 122px; background: linear-gradient(to bottom, rgba(247,148,29,0) 0%, rgba(247,148,29,0.55) 35%, var(--orange) 100%); }
  .field--grey { top: 296px; height: 122px; background: linear-gradient(to bottom, rgba(88,89,91,0) 0%, rgba(88,89,91,0.55) 35%, var(--charcoal) 100%); }

  .band {
    position: absolute;
    left: 0; right: 0; bottom: 0;
    height: 60px;
    display: flex;
    align-items: center;
    justify-content: center;
    gap: 18px;
    color: #fff;
  }
  .band--orange { background: var(--orange); height: 58px; }
  .band--grey { background: var(--charcoal); height: 64px; }
  .band__rule { flex: 0 0 154px; height: 2px; background: #fff; }
  .tagline {
    font-weight: 900;
    font-style: italic;
    font-size: 37px;
    letter-spacing: 0.5px;
    margin-top: -28px;
  }

  .services { position: absolute; left: 41px; top: 40px; list-style: none; }
  .service { position: relative; padding-left: 46px; margin-bottom: 8px; }
  .service__dot {
    position: absolute; left: 0; top: 8px;
    width: 14px; height: 14px; border-radius: 50%;
    background: var(--orange);
  }
  .service__title { color: var(--orange); font-weight: 700; font-size: 23px; line-height: 30px; }
  .service__title em { color: var(--ink); font-weight: 400; font-style: italic; }
  .service__detail { color: var(--ink); font-size: 22px; line-height: 30px; }

  .back__mark { left: 665px; top: 18px; width: 96px; height: 96px; }
  .back__name { left: 555px; right: 12px; top: 116px; font-size: 27px; letter-spacing: -0.3px; }
  .back__sub { left: 555px; right: 12px; top: 144px; font-size: 13px; letter-spacing: 3px; }

  .contact {
    display: flex; align-items: center; gap: 16px;
    font-weight: 900; font-style: italic; font-size: 35px;
    margin-top: -6px;
  }
  .contact__icon { width: 38px; height: 38px; }
</style>
</head>
<body>

<section class="card card--front">
  <div class="brand-mark front__mark"></div>
  <p class="brand-name front__name">Halloran Field</p>
  <p class="brand-name front__sub">SERVICES</p>
  <div class="field field--gold" role="img" aria-label="Silhouette of tall pasture grass in orange"></div>
  <div class="band band--orange">
    <span class="band__rule"></span>
    <span class="tagline">CUSTOMIZED SPREADING</span>
    <span class="band__rule"></span>
  </div>
</section>

<section class="card card--back">
  <ul class="services">
    <li class="service">
      <span class="service__dot"></span>
      <p class="service__title">BULK FERTILIZER <em>including</em></p>
      <p class="service__detail">Lime, Gypsum, Manure &amp; Compost</p>
    </li>
    <li class="service">
      <span class="service__dot"></span>
      <p class="service__title">MODERN EQUIPMENT</p>
      <p class="service__detail">Autosteer &amp; Variable Rate Capable</p>
    </li>
    <li class="service">
      <span class="service__dot"></span>
      <p class="service__title">GRANULAR FERTILIZER <em>including</em></p>
      <p class="service__detail">Single Super, Urea, Gran-am, &amp; Custom Blends</p>
    </li>
    <li class="service">
      <span class="service__dot"></span>
      <p class="service__title">FRIENDLY &amp; RELIABLE SERVICES</p>
    </li>
  </ul>

  <div class="brand-mark back__mark"></div>
  <p class="brand-name back__name">Halloran Field</p>
  <p class="brand-name back__sub">SERVICES</p>

  <div class="field field--grey" role="img" aria-label="Silhouette of tall pasture grass in charcoal"></div>
  <div class="band band--grey">
    <div class="contact">
      <span>Call GUS</span>
      <svg class="contact__icon" viewBox="0 0 40 40" aria-hidden="true">
        <circle cx="20" cy="20" r="19" fill="var(--orange)"/>
        <path d="M14 11c1-1 2.5-1 3 0l2 4c.4.8.1 1.6-.5 2.1l-1.3 1c1 2.3 2.6 3.9 4.8 4.9l1-1.3c.5-.7 1.4-.9 2.1-.5l4 2c1 .5 1 2 0 3l-1.6 1.6c-1.2 1.2-3 1.5-4.5.8C17.5 26.5 13.5 22.5 11.4 17c-.6-1.5-.3-3.3.9-4.4z" fill="#fff"/>
      </svg>
      <span>0417 552 308</span>
    </div>
  </div>
</section>

</body>
</html>
```